Medical centre needs a business card

We are a medcial centre in Australia, needing a new business card. Our demographic is low working class families. We are going to be renovating our premises to modernise the look and also had a new logo done a few months ago representing quality and community, and now need to update our cards. It needs to be doubled sided, with logo and contact details on the front, and appointment details on the back. . Needs to be modern and simple, easy to read. <br/><br/>Name: Kindle Grove Medical Centre <br/>Address: 512 Parmley Rd (Cnr Parmley Rd & Osgood Creek Rd),<br/>Tindarra Court Shopping Centre, Marlow Heights, SA 5990<br/>Ph: 08 8461 3072<br/>Tag line: Where your wellbeing comes first<br/>Website: www.kindlegrovemedicalcentre-example.com.au<br/>Online bookings also available<br/><br/>(On the back, to have 3 lines of appointments that can be written in.<br/>Day, date, time)<br/><br/>Your next appointment is on<br/>Can try “M T W Th F Sa Su _________________ at ____________ am/pm” or other combinations <br/>Please advise as soon as possible if unable to attend<br/>Cancellation fees apply if less than 2 hrs notice<br/>Online appointments available (please highlight this option by either by position, colour or font)

Target Market(s)

Lower social economic working class, young families to seniors

Industry/Entity Type

Medical Centre

Contact Information for Business Card

Kindle Grove Medical Centre
512 Parmley Rd (Cnr Parmley Rd & Osgood Creek Drive)
Tindarra Court Shopping Centre
Marlow Heights SA 5990
Ph: 08 8461 3072
www.kindlegrovemedicalcentre-example.com.au
Tagline line: where your wellbeing comes first
Back side is for appointments
Your next appointment is with Dr ______________
Day/date/time (Please give 3 lines of appointments)
Please advise as soon as possible if unable to attend
Cancellation fees apply if less than 2 hours notice
Online appointments available
Book online easily and conveniently (please highlight online appointments)

Font styles to use
Serif
Sans Serif

Colors

Designer to choose colors to be used in the design.

Requirements
Must have
• Modern and simple
• Easy to ready
• Induces a wellbeing feeling
• Incorporate our logo colours and feel from logo
• Induces feeling of stability and security
Nice to have
• Attract attention
• Pleasant to look at
• Feeling of innovation
Should not have
• Loud clashing colours
• Overly luxurious feeling
• Overly artistic

```html
<!DOCTYPE html>
<html lang="en">
<head>
<meta charset="utf-8">
<title>Kindle Grove Medical Centre – Business Card</title>
<link href="https://fonts.googleapis.com/css2?family=Asap+Condensed:wght@400;500;600;700&display=swap" rel="stylesheet">
<style>
  :root{
    --blue:#1779cf;
    --blue-dark:#0f63b0;
    --green:#8cc63f;
    --white:#ffffff;
    --page:#eef0f2;
    --ink:#1779cf;
  }
  *{box-sizing:border-box;margin:0;padding:0}
  html,body{width:1200px;height:800px;overflow:hidden}
  body{
    background:var(--page);
    font-family:"Asap Condensed",sans-serif;
    color:var(--ink);
    display:flex;align-items:center;justify-content:center;gap:44px;
  }
  .card{
    position:relative;width:530px;height:324px;background:var(--white);
    box-shadow:0 6px 22px rgba(0,0,0,.12);overflow:hidden;
  }
  .band-right{position:absolute;top:0;right:0;width:26px;height:100%;background:var(--green)}
  .band-bottom{position:absolute;left:0;bottom:0;width:260px;height:16px}

  /* front */
  .brand{position:absolute;left:90px;top:56px;display:flex;align-items:center;gap:12px}
  .brand-mark{width:34px;height:34px;border-radius:50%;background:var(--green);flex:none}
  .brand-name{font-size:27px;font-weight:700;color:var(--blue);line-height:1;letter-spacing:.3px;white-space:nowrap}
  .tagline{position:absolute;left:136px;top:94px;font-size:14px;font-weight:500;color:var(--blue);letter-spacing:.6px}

  .contacts{position:absolute;right:60px;bottom:38px;text-align:right;line-height:1.2}
  .contacts .phone{font-size:22px;font-weight:700}
  .contacts .email{font-size:16px;font-weight:500;margin-top:2px}
  .contacts .web{font-size:15px;font-weight:600;margin-top:4px}
  .contacts .addr{font-size:12px;font-weight:500;margin-top:4px}
  .icons{position:absolute;right:30px;bottom:38px;display:flex;flex-direction:column;gap:4px}
  .icon{width:26px;height:26px;background:var(--blue);display:flex;align-items:center;justify-content:center}
  .icon svg{width:16px;height:16px}

  /* back */
  .appt{position:absolute;left:30px;top:26px;right:52px;font-size:18px;font-weight:600}
  .row{display:flex;align-items:flex-end;gap:6px;margin-bottom:10px}
  .fill{flex:1;border-bottom:1.2px solid var(--blue);height:16px}
  .days{display:flex;justify-content:space-between;margin:0 0 12px;font-size:17px}
  .day::before{content:"";display:inline-block;width:10px;height:10px;border:1.3px solid var(--blue);margin-right:5px;vertical-align:1px}
  .dot{width:11px;height:11px;border-radius:50%;background:var(--blue);align-self:center;flex:none}
  .fill.date{flex:1.3}
  .notes{position:absolute;left:30px;top:204px;font-size:16px;font-weight:500;line-height:1.3}
  .online{
    position:absolute;left:30px;top:254px;background:var(--blue-dark);color:var(--white);
    font-size:15px;font-weight:700;letter-spacing:1px;text-transform:uppercase;
    padding:6px 26px;border-radius:14px;
  }
</style>
</head>
<body>

<section class="card card-front" aria-label="Card front">
  <div class="brand">
    <span class="brand-mark"></span>
    <span class="brand-name">Kindle Grove Medical Centre</span>
  </div>
  <p class="tagline">Where your wellbeing comes first</p>

  <div class="contacts">
    <p class="phone">08 8461 3072</p>
    <p class="email">hello@kindlegrove-example.com.au</p>
    <p class="web">www.kindlegrovemedicalcentre-example.com.au</p>
    <p class="addr">512 Parmley Rd (Cnr Parmley Rd &amp; Osgood Creek Drive)<br>Tindarra Court Shopping Centre, Marlow Heights, SA 5990</p>
  </div>

  <div class="icons">
    <span class="icon"><svg viewBox="0 0 24 24" fill="#fff"><path d="M6.6 10.8a15 15 0 0 0 6.6 6.6l2.2-2.2c.3-.3.7-.4 1-.2 1.1.4 2.3.6 3.6.6.6 0 1 .4 1 1V20c0 .6-.4 1-1 1A17 17 0 0 1 3 4c0-.6.4-1 1-1h3.5c.6 0 1 .4 1 1 0 1.3.2 2.5.6 3.6.1.3 0 .7-.2 1z"/></svg></span>
    <span class="icon"><svg viewBox="0 0 24 24" fill="none" stroke="#fff" stroke-width="2"><rect x="3" y="5" width="18" height="14"/><path d="M3 5l9 8 9-8"/></svg></span>
    <span class="icon"><svg viewBox="0 0 24 24" fill="none" stroke="#fff" stroke-width="1.8"><circle cx="12" cy="12" r="9"/><path d="M3 12h18M12 3c3 3 3 15 0 18M12 3c-3 3-3 15 0 18"/></svg></span>
    <span class="icon"><svg viewBox="0 0 24 24" fill="#fff"><path d="M12 2a7 7 0 0 0-7 7c0 5 7 13 7 13s7-8 7-13a7 7 0 0 0-7-7zm0 9.5A2.5 2.5 0 1 1 12 6.5a2.5 2.5 0 0 1 0 5z"/></svg></span>
  </div>

  <div class="band-right"></div>
  <svg class="band-bottom" viewBox="0 0 260 16" preserveAspectRatio="none" aria-hidden="true">
    <polygon points="0,0 118,0 118,16 0,16" fill="#1779cf"/>
    <polygon points="118,0 248,0 260,16 118,16" fill="#8cc63f"/>
  </svg>
</section>

<section class="card card-back" aria-label="Card back">
  <div class="appt">
    <div class="row"><span>Your next appointment is with: Dr.</span><span class="fill"></span></div>
    <div class="days">
      <span class="day">Mon</span><span class="day">Tue</span><span class="day">Wed</span><span class="day">Thu</span><span class="day">Fri</span><span class="day">Sat</span><span class="day">Sun</span>
    </div>
    <div class="row"><span class="dot"></span><span>Date:</span><span class="fill date"></span><span>Time:</span><span class="fill"></span><span>am/pm</span></div>
    <div class="row"><span class="dot"></span><span>Date:</span><span class="fill date"></span><span>Time:</span><span class="fill"></span><span>am/pm</span></div>
    <div class="row"><span class="dot"></span><span>Date:</span><span class="fill date"></span><span>Time:</span><span class="fill"></span><span>am/pm</span></div>
  </div>

  <p class="notes">Please advise as soon as possible if unable to attend<br>Cancellation fees apply if less than 2 hours notice</p>
  <p class="online">Online appointments available</p>

  <div class="band-right"></div>
  <svg class="band-bottom" viewBox="0 0 260 16" preserveAspectRatio="none" aria-hidden="true">
    <polygon points="0,0 118,0 118,16 0,16" fill="#1779cf"/>
    <polygon points="118,0 248,0 260,16 118,16" fill="#8cc63f"/>
  </svg>
</section>

</body>
</html>
```